Salon and Spa Distributor Business Card

Need a business card. We are are distributor in the salon and spa industry. We identify with natural beauty. Need a card with:
Company Name: Petal Quarry"
Title: "President & CEO"
Address
Company Phone number
email
website
Tag Line:" The Professional Salon Source"

Industry/Entity Type

Business

Contact Information for Business Card

Name: Dov Strommen
Title: "President & CEO"
Address: 31 Harlow Ln, Bexmoor, NJ 07813
Company Phone number: 800-463-5918
email: dovstrommen@petalquarry.example
website: www.petalquarry.example

Requirements
Should not have
• No black backgrounds

```html
<!DOCTYPE html>
<html lang="en">
<head>
<meta charset="utf-8">
<title>Petal Quarry — Business Card</title>
<link href="https://fonts.googleapis.com/css2?family=Questrial&family=Arimo:wght@700&display=swap" rel="stylesheet">
<style>
  :root {
    --stage: #000000;
    --card-front: #ffffff;
    --card-back: #f7f7f7;
    --brand-green: #3f9142;
    --ink: #222222;
    --rule: #d9e3d9;
  }
  * { margin: 0; padding: 0; box-sizing: border-box; }
  html, body {
    width: 1200px; height: 900px; overflow: hidden;
    background: var(--stage);
    font-family: "Questrial", "Century Gothic", sans-serif;
  }
  .canvas { position: relative; width: 1200px; height: 900px; }
  .card {
    position: absolute; top: 192px; height: 491px;
    border-radius: 14px; overflow: hidden;
  }
  .card--front { left: 295px; width: 301px; background: var(--card-front); }
  .card--back { left: 621px; width: 305px; background: var(--card-back); }

  .front-content { position: absolute; inset: 0; text-align: center; }
  .company-name {
    position: absolute; top: 104px; left: 0; right: 0;
    font-size: 36px; color: var(--brand-green); letter-spacing: 0.2px;
  }
  .tagline {
    position: absolute; top: 161px; left: 0; right: 0;
    font-size: 16.5px; color: var(--brand-green);
  }
  .person-name {
    position: absolute; top: 245px; left: 0; right: 0;
    font-family: "Arimo", Arial, sans-serif; font-weight: 700;
    font-size: 26px; color: var(--brand-green);
  }
  .person-title {
    position: absolute; top: 277px; left: 0; right: 0;
    font-size: 14px; color: var(--ink);
  }
  .rule {
    position: absolute; left: 45px; right: 45px; height: 1px;
    background: linear-gradient(90deg, transparent, var(--rule) 25%, var(--rule) 75%, transparent);
  }
  .rule--upper { top: 301px; }
  .rule--lower { top: 378px; }
  .contact-list {
    position: absolute; top: 309px; left: 0; right: 0;
    list-style: none; font-size: 14.5px; line-height: 20.5px; color: var(--ink);
  }
  .contact-label { color: var(--brand-green); font-weight: 700; }
  .address {
    position: absolute; top: 387px; left: 0; right: 0;
    font-size: 14.5px; line-height: 18px; color: var(--ink); font-style: normal;
  }

  .back-brand {
    position: absolute; top: 232px; left: 0; right: 0;
    display: flex; align-items: center; justify-content: center; gap: 10px;
  }
  .brand-dot { width: 22px; height: 22px; border-radius: 50%; background: var(--brand-green); }
  .back-name { font-size: 22px; color: var(--brand-green); }
</style>
</head>
<body>
  <main class="canvas">
    <section class="card card--front" aria-label="Business card front">
      <div class="front-content">
        <h1 class="company-name">Petal Quarry</h1>
        <p class="tagline">The Professional Salon Source</p>
        <h2 class="person-name">Dov Strommen</h2>
        <p class="person-title">President &amp; CEO</p>
        <div class="rule rule--upper"></div>
        <ul class="contact-list">
          <li><span class="contact-label">P:</span> 800-463-5918</li>
          <li><span class="contact-label">E:</span> dovstrommen@petalquarry.example</li>
          <li>www.petalquarry.example</li>
        </ul>
        <div class="rule rule--lower"></div>
        <address class="address">31 Harlow Ln, Bexmoor,<br>NJ 07813</address>
      </div>
    </section>

    <section class="card card--back" aria-label="Business card back">
      <div class="back-brand">
        <span class="brand-dot"></span>
        <span class="back-name">Petal Quarry</span>
      </div>
    </section>
  </main>
</body>
</html>
```